Business Cards for new orthopaedic surgery practice

My husband and I are starting our own orthopaedic surgery practice. We are looking for a business card that is uniform, but one will have my name/title and the other will have his. You can just create one design with my name on it for now. But when I choose your design as the winning design I will ask that you add another copy with his name/title.

We are looking for classy, simple, elite all in one. We like dark blues/a little gold/yellow. Something that goes with our logo. We want our logo incorporated. Here is all the info you need:
Business name: RV Bone & Vitality Center
Location: 38517 North Willowmere Ave
Palm Hollow, FL 33490
Phone: 954-218-4063
Fax: 954-582-7341
Email: info@myrvbonecare.example

Names: Lydia Vance, M.D.
Board Certified Hand and Upper Extremity Surgeon

Ebo Dansu, M.D.
Board Certified Hip & Knee Replacement/General Orthopaedic Surgeon

Can decide what you want to put on the back. Maybe a slogan:
Grounded in Care. Centered on You

I am just going to upload our logo. The only thing is if we select you as the winning design, the location, and phone numbers may change. We will need your help to update that once fully solidified.

Industry/Entity Type

Medical

Contact Information for Business Card

Colors
0054AA
0677BA
7BADD7
CADEEF
E8F1F8
0094D4
00A9DD
6FCCEA
C7EBF8
E9F6FB

Requirements
Must have
• class, appeal,
Should not have
• We want to air on the side of masculine if we are looking at masculine vs. feminine feel. But we still want it classy, sophisticated, and something we will love

```html
<!DOCTYPE html>
<html lang="en">
<head>
<meta charset="utf-8">
<title>RV Bone &amp; Vitality Center — Business Cards</title>
<link href="https://fonts.googleapis.com/css2?family=Cinzel:wght@700&family=Montserrat:wght@400;500;600&display=swap" rel="stylesheet">
<style>
  :root {
    --navy: #1b2a52;
    --gold: #c9a04f;
    --white: #ffffff;
    --ink: #2f3a55;
    --backdrop: #bdbdbd;
  }
  * { box-sizing: border-box; margin: 0; padding: 0; }
  html, body { width: 1200px; height: 802px; overflow: hidden; }
  body {
    background: var(--backdrop);
    font-family: "Montserrat", sans-serif;
    display: flex; align-items: center; justify-content: center; gap: 40px;
  }
  .card {
    position: relative; width: 540px; height: 309px;
    border-radius: 18px; overflow: hidden;
    box-shadow: 0 10px 24px rgba(0,0,0,.25);
  }
  .card-front { background: var(--white); }
  .card-back { background: var(--navy); }
  .front-band { position: absolute; inset: 0; }
  .brand-mark {
    position: absolute; width: 120px; height: 120px; border-radius: 50%;
    border: 1.5px solid var(--gold);
    display: flex; align-items: center; justify-content: center; text-align: center;
    font-weight: 600; letter-spacing: .08em; text-transform: uppercase; line-height: 1.35;
  }
  .card-front .brand-mark { left: 88px; top: 30px; color: var(--navy); font-size: 12px; padding: 14px; }
  .card-back .brand-mark {
    left: 190px; top: 46px; width: 160px; height: 160px;
    color: var(--white); font-size: 15px; padding: 20px;
  }
  .divider { position: absolute; left: 282px; top: 56px; width: 1.5px; height: 106px; background: var(--gold); }
  .contacts { position: absolute; left: 300px; top: 60px; list-style: none; color: var(--ink); font-size: 13px; }
  .contacts li { display: flex; align-items: center; gap: 8px; height: 27px; }
  .contacts svg { width: 12px; height: 12px; fill: var(--gold); flex: none; }
  .doctor { position: absolute; left: 34px; top: 172px; }
  .doctor-name { font-family: "Cinzel", serif; font-weight: 700; font-size: 19px; color: var(--navy); letter-spacing: .02em; }
  .doctor-name .credential { color: var(--gold); }
  .doctor-title { font-size: 12.5px; color: var(--ink); line-height: 1.4; margin-top: 4px; }
  .address { position: absolute; right: 26px; bottom: 22px; color: var(--white); font-size: 12.5px; letter-spacing: .02em; }
  .tagline {
    position: absolute; left: 0; right: 0; top: 236px; text-align: center;
    color: var(--gold); font-weight: 600; font-size: 17px; letter-spacing: .02em;
  }
</style>
</head>
<body>
  <section class="card card-front">
    <svg class="front-band" viewBox="0 0 540 309" preserveAspectRatio="none" aria-hidden="true">
      <path d="M0,262 Q330,255 540,148 L540,309 L0,309 Z" fill="var(--navy)"/>
      <path d="M0,256 Q328,249 540,140" fill="none" stroke="var(--gold)" stroke-width="2"/>
    </svg>
    <div class="brand-mark">RV Bone &amp; Vitality Center</div>
    <div class="divider"></div>
    <ul class="contacts">
      <li><svg viewBox="0 0 24 24"><path d="M6.6 10.8a15 15 0 0 0 6.6 6.6l2.2-2.2a1 1 0 0 1 1-.25 11.4 11.4 0 0 0 3.6.6 1 1 0 0 1 1 1V20a1 1 0 0 1-1 1A17 17 0 0 1 3 4a1 1 0 0 1 1-1h3.5a1 1 0 0 1 1 1c0 1.25.2 2.45.57 3.57a1 1 0 0 1-.25 1z"/></svg>954-218-4063</li>
      <li><svg viewBox="0 0 24 24"><path d="M7 3h10v5H7zM4 9h16a2 2 0 0 1 2 2v6h-4v4H6v-4H2v-6a2 2 0 0 1 2-2zm4 7v3h8v-3z"/></svg>954-582-7341</li>
      <li><svg viewBox="0 0 24 24"><path d="M2 5h20v14H2zm2 2v.5l8 5 8-5V7z"/></svg>info@myrvbonecare.example</li>
    </ul>
    <div class="doctor">
      <h1 class="doctor-name">LYDIA VANCE, <span class="credential">M.D.</span></h1>
      <p class="doctor-title">Board Certified Hand and<br>Upper Extremity Surgeon</p>
    </div>
    <p class="address">38517 North Willowmere Ave Palm Hollow, FL 33490</p>
  </section>

  <section class="card card-back">
    <div class="brand-mark">RV Bone &amp; Vitality Center</div>
    <p class="tagline">Grounded in Care. Centered on You</p>
  </section>
</body>
</html>
```